Business Card Design

We need the business card for our new business based in St. Marys, we manufacture mainly bubble wraps. And we would like the design to use our company logo and also make it easy for people to understand right away we are bubble wrap manufacturer

Industry/Entity Type

Business

Contact Information for Business Card

Cushtane Pty Ltd, 14 Larkin Road Brenmore NSW 2768, Tel: 02 9471 5826, Fax: 9471 5839, Dara Oyelaran, General Manager, Mobile :0438 217 564, dara.oyelaran@cushtane.com.au, Website: cushtane.com.au

```html
<!DOCTYPE html>
<html lang="en">
<head>
<meta charset="utf-8">
<title>Cushtane Business Card</title>
<link href="https://fonts.googleapis.com/css2?family=Arimo:wght@400;700&display=swap" rel="stylesheet">
<style>
  :root {
    --page-bg: #e9e6e2;
    --card-white: #ffffff;
    --band-black: #000000;
    --brand-grey: #707070;
    --accent-red: #c4262e;
    --ink: #111111;
    --rule: #222222;
  }
  * { margin: 0; padding: 0; box-sizing: border-box; }
  html, body {
    width: 1200px; height: 914px; overflow: hidden;
    background: var(--page-bg);
    font-family: "Arimo", Arial, sans-serif;
  }
  .canvas { position: relative; width: 1200px; height: 914px; }

  .card {
    position: absolute;
    width: 560px; height: 342px;
    background: var(--card-white);
    overflow: hidden;
    box-shadow: 0 6px 18px rgba(0,0,0,0.18);
  }
  .card--back { left: 560px; top: 90px; }
  .card--front { left: 80px; top: 480px; }

  .band { position: absolute; left: 0; width: 100%; background: var(--band-black); }
  .card--back .band--top { top: 0; height: 44px; }
  .card--back .band--bottom { bottom: 0; height: 72px; }
  .card--front .band--bottom { bottom: 0; height: 116px; }

  .brand { position: absolute; left: 0; width: 100%; text-align: center; }
  .brand__name {
    font-weight: 700; color: var(--brand-grey);
    font-size: 46px; letter-spacing: 1px; line-height: 1;
  }
  .brand__tagline {
    margin-top: 6px;
    font-size: 10px; letter-spacing: 3.4px; text-transform: uppercase;
    color: var(--brand-grey);
  }
  .card--back .brand { top: 128px; }
  .card--front .brand { top: 26px; }

  .contact-box {
    position: absolute; left: 140px; top: 118px;
    width: 280px; height: 178px;
    background: var(--card-white);
    border: 1.5px solid var(--rule);
    text-align: center;
    padding-top: 10px;
  }
  .person__name { color: var(--accent-red); font-size: 26px; line-height: 1.05; }
  .person__title { color: var(--brand-grey); font-size: 14px; margin-top: 2px; }

  .details { margin: 10px auto 0; border-collapse: collapse; font-size: 13px; line-height: 1.32; }
  .details th { text-align: right; font-weight: 400; color: var(--ink); padding-right: 6px; white-space: nowrap; }
  .details td { text-align: left; color: var(--accent-red); white-space: nowrap; }

  .address {
    position: absolute; left: 30px; bottom: 18px;
    color: var(--accent-red); font-size: 14px; white-space: nowrap;
  }
</style>
</head>
<body>
<main class="canvas">

  <section class="card card--back" aria-label="Card back">
    <div class="band band--top"></div>
    <div class="brand">
      <div class="brand__name">CUSHTANE</div>
      <div class="brand__tagline">Protective Packaging Solutions</div>
    </div>
    <div class="band band--bottom"></div>
  </section>

  <section class="card card--front" aria-label="Card front">
    <div class="brand">
      <div class="brand__name">CUSHTANE</div>
      <div class="brand__tagline">Protective Packaging Solutions</div>
    </div>
    <div class="band band--bottom"></div>
    <div class="contact-box">
      <div class="person__name">Dara Oyelaran</div>
      <div class="person__title">General Manager</div>
      <table class="details">
        <tr><th>Phone :</th><td>02 9471 5826</td></tr>
        <tr><th>Cell :</th><td>0438 217 564</td></tr>
        <tr><th>Fax :</th><td>9471 5839</td></tr>
        <tr><th>Web :</th><td>www.cushtane.com.au</td></tr>
        <tr><th>Email :</th><td>dara.oyelaran@cushtane.com.au</td></tr>
      </table>
    </div>
    <p class="address">Cushtane Pty Ltd, 14 Larkin Road Brenmore NSW 2768</p>
  </section>

</main>
</body>
</html>
```